Development of the overall look and feel for the website. www.ReelPalsHub.com

This site is geared as a competitor to some of the major Fan websites. Where we want to be different is making a site geared more towards interaction with the Fans in the Social Media platform.
-Live streaming
-Instant Messaging
-Ability to request and purchase custom digital pieces
-Ability for Models/creators to sell blogs, podcasts, clips, screensavers, etc. through a dedicated online digital store.
-We will also have story like features similar to those found on Photoburst to allow interaction.
-Content Creators keep 85% of earnings

This should be sexy, seductive, bold, and geared towards all spectrums. From Swingers, Kink, Fetish, Milf, College, etc.

Overall the feeling should be Fun with a sense of excitement that is taboo and erotic while not scaring people away.

Trying to find the perfect blend between finding harmony/Norma Whitcombe/GBT/SoloPatron/Velvet Soiree and KRV. Monetization will be most similar to SoloPatron.

Target Market(s)

Target market should be 18+ / All Genders/ All sexuality. I want to be sure to target markets that were traditionally left out from some of the bigger platforms with all lifestyle and gender inclusion.

Industry/Entity Type

Adult Modeling, Adult Website, Streaming, Porn/fetish

Colors

Designer to choose colors to be used in the design.

Requirements
Must have
• Sex Appeal, Curiosity, Call to action, Storyboard to tell what we are about
Nice to have
• uploaded some designs that have overall look/feel.
Should not have
• Sexy but no nudity

```html
<!DOCTYPE html>
<html lang="en">
<head>
<meta charset="utf-8">
<title>ReelPalsHub – Live Call</title>
<link rel="stylesheet" href="https://fonts.googleapis.com/css2?family=Lato:wght@400;700;900&display=swap">
<style>
:root{
  --bg-top:#e56b78;
  --bg-bottom:#862f72;
  --card:#ffffff;
  --ink:#1e1e24;
  --muted:#6b6b78;
  --plum:#7b2d6f;
  --rose:#e5606d;
  --end-call:#e24855;
  --panel:#eef0f6;
  --line:#e4e5ec;
  --tile:#e6e7ec;
  --tile-edge:#b9bac4;
}
*{box-sizing:border-box;margin:0;padding:0}
html,body{width:1200px;height:698px;overflow:hidden}
body{font-family:"Lato",sans-serif;color:var(--ink);background:linear-gradient(180deg,var(--bg-top) 0%,#c94f77 45%,var(--bg-bottom) 100%);position:relative}
.app{position:absolute;left:40px;top:34px;width:1125px;height:621px;background:var(--card);border-radius:34px;overflow:hidden}
.sidebar{position:absolute;left:0;top:0;width:146px;height:100%;border-right:1px solid var(--line)}
.brand{position:absolute;left:17px;top:14px;width:94px;height:94px;border-radius:50%;background:#fff;box-shadow:0 4px 12px rgba(0,0,0,.15);display:flex;align-items:center;justify-content:center;font-size:11px;font-weight:700;color:var(--plum)}
.nav{position:absolute;left:0;top:153px;width:146px;display:flex;flex-direction:column;align-items:center}
.nav-item{display:flex;flex-direction:column;align-items:center;margin-bottom:9px}
.nav-icon{width:44px;height:40px;border-radius:6px;background:var(--tile);border:1px solid var(--tile-edge);display:flex;align-items:center;justify-content:center}
.nav-icon.active{background:var(--plum);border-color:var(--plum)}
.nav-label{font-size:15px;margin-top:6px}
.user-avatar{position:absolute;left:48px;top:553px;width:36px;height:36px;border-radius:50%;background:radial-gradient(circle at 50% 40%,#e9c0a4 0 30%,#2f6fc4 31%);box-shadow:0 2px 6px rgba(0,0,0,.15)}
.topbar{position:absolute;left:147px;top:0;width:675px;height:56px;border-bottom:1px solid var(--line);display:flex;align-items:center}
.back{margin-left:23px;width:20px;height:20px}
.title{margin-left:10px;font-size:16px}
.pro{margin-left:24px;height:27px;padding:0 14px;border-radius:14px;background:var(--plum);color:#fff;display:flex;align-items:center;gap:8px;font-size:16px}
.stage{position:absolute;left:168px;top:79px;width:640px;height:457px;border-radius:32px;overflow:hidden}
.stage-media{position:absolute;inset:0;background:radial-gradient(ellipse at 55% 55%,#8a6a5a 0%,#3a2a28 45%,#141214 100%)}
.volume{position:absolute;left:21px;top:236px;width:57px;height:187px;border-radius:28px;background:rgba(255,255,255,.22)}
.volume-track{position:absolute;left:27px;top:20px;width:3px;height:115px;background:linear-gradient(#e24855,#7b2d6f);border-radius:2px}
.volume-knob{position:absolute;left:21px;top:76px;width:15px;height:15px;border-radius:50%;background:#fff}
.volume-icon{position:absolute;left:20px;top:150px}
.ctrl{position:absolute;top:368px;width:52px;height:52px;border-radius:50%;background:rgba(120,120,128,.75);display:flex;align-items:center;justify-content:center}
.end-call{position:absolute;left:265px;top:359px;width:109px;height:63px;border-radius:12px;background:var(--end-call);display:flex;align-items:center;justify-content:center}
.now{position:absolute;left:190px;top:553px;display:flex;align-items:center;gap:13px}
.now-head{font-size:16px}
.now-text{font-size:12px;font-weight:700;margin-top:4px}
.chat{position:absolute;left:826px;top:14px;width:280px;height:583px;background:var(--panel);border-radius:12px}
.chat-head{height:50px;border-bottom:1px solid #d8dae3;display:flex;align-items:center;padding-left:12px}
.chat-title{font-size:17px;font-weight:700;margin-right:14px}
.tab{font-size:12px;padding:7px 18px;border-radius:14px}
.tab.active{background:var(--rose);color:#fff}
.messages{padding:10px 12px 0 12px}
.msg{display:flex;align-items:flex-end;gap:8px;margin-bottom:7px}
.sender{font-size:7px;font-weight:700;margin:0 0 3px 48px}
.avatar{width:28px;height:28px;border-radius:50%;flex:none;box-shadow:0 1px 3px rgba(0,0,0,.2)}
.avatar.blue{background:radial-gradient(circle at 50% 38%,#e9c0a4 0 28%,#2f6fc4 29%)}
.avatar.amber{background:radial-gradient(circle at 50% 40%,#f2d2b4 0 28%,#f0a030 29%)}
.bubble{background:#fff;border-radius:8px;padding:10px 11px;font-size:10px;font-weight:700;color:#3a3a44;box-shadow:0 1px 2px rgba(0,0,0,.05)}
.bubble.call{display:flex;align-items:center;gap:8px;color:#9a9aa6;padding:6px 11px 6px 6px}
.call-icon{width:26px;height:26px;border-radius:6px;background:#d6f2ea;display:flex;align-items:center;justify-content:center}
.composer{position:absolute;left:11px;top:524px;width:258px;height:46px;background:#fff;border-radius:8px;display:flex;align-items:center;justify-content:space-between;padding:0 7px 0 12px;font-size:10px}
.send{width:35px;height:35px;border-radius:6px;background:var(--plum);display:flex;align-items:center;justify-content:center}
</style>
</head>
<body>
<main class="app">
  <aside class="sidebar">
    <div class="brand">ReelPalsHub</div>
    <nav class="nav">
      <div class="nav-item"><div class="nav-icon active"><svg width="24" height="22" viewBox="0 0 24 22" fill="none" stroke="#fff" stroke-width="1.5"><rect x="3" y="2" width="18" height="13" rx="1.5"/><circle cx="9" cy="8" r="2.5"/><path d="M5 15c0-3 8-3 8 0M9 19h6"/></svg></div><span class="nav-label">Models/creators</span></div>
      <div class="nav-item"><div class="nav-icon"><svg width="24" height="22" viewBox="0 0 24 22" fill="none" stroke="#333" stroke-width="1.3"><rect x="7" y="2" width="12" height="13" rx="1"/><path d="M9 6h8M9 9h8M9 12h6"/><rect x="2" y="14" width="10" height="5" rx="2.5"/></svg></div><span class="nav-label">Sell blogs</span></div>
      <div class="nav-item"><div class="nav-icon"><svg width="24" height="24" viewBox="0 0 24 24" fill="none" stroke="#333" stroke-width="1.3"><rect x="9" y="3" width="6" height="11" rx="3"/><path d="M6 11a6 6 0 0 0 12 0M12 17v4M8 21h8M3 8v6M21 8v6"/></svg></div><span class="nav-label">Podcasts</span></div>
      <div class="nav-item"><div class="nav-icon"><svg width="22" height="22" viewBox="0 0 24 24" fill="none" stroke="#333" stroke-width="1.5"><path d="M17 7l-8 8a2 2 0 0 1-3-3l9-9a3.5 3.5 0 0 1 5 5l-9 9a5 5 0 0 1-7-7l8-8"/></svg></div><span class="nav-label">Clips</span></div>
      <div class="nav-item"><div class="nav-icon"><svg width="26" height="22" viewBox="0 0 26 22" fill="none" stroke="#333" stroke-width="1.3"><rect x="2" y="2" width="22" height="14" rx="1"/><circle cx="13" cy="9" r="3.5"/><path d="M8 19h10"/></svg></div><span class="nav-label">Screensavers</span></div>
    </nav>
    <div class="user-avatar" role="img" aria-label="Signed-in user avatar"></div>
  </aside>

  <header class="topbar">
    <svg class="back" viewBox="0 0 20 20"><circle cx="10" cy="10" r="10" fill="#d6d7dd"/><path d="M11 5l-5 5 5 5M6 10h8" stroke="#fff" stroke-width="2.2" fill="none"/></svg>
    <h1 class="title" style="font-weight:400">Lorem ipsum dolor sit amet, consectetur</h1>
    <span class="pro"><svg width="14" height="14" viewBox="0 0 14 14" fill="#fff"><circle cx="7" cy="4" r="3.2"/><path d="M1 14c0-4 12-4 12 0z"/></svg>Pro</span>
  </header>

  <section class="stage">
    <div class="stage-media" role="img" aria-label="Live stream video feed of a model in black lace holding a red rope"></div>
    <div class="volume">
      <div class="volume-track"></div><div class="volume-knob"></div>
      <svg class="volume-icon" width="18" height="20" viewBox="0 0 18 20" fill="#fff"><path d="M2 7h4l6-5v16l-6-5H2z"/></svg>
    </div>
    <div class="ctrl" style="left:117px"><svg width="18" height="18" viewBox="0 0 18 18" stroke="#fff" stroke-width="2" fill="none"><path d="M2 6V2h4M12 2h4v4M16 12v4h-4M6 16H2v-4"/></svg></div>
    <div class="ctrl" style="left:190px"><svg width="18" height="20" viewBox="0 0 18 20" stroke="#fff" stroke-width="2" fill="none"><rect x="6" y="2" width="6" height="10" rx="3"/><path d="M3 10a6 6 0 0 0 12 0M9 16v3M3 18L16 3"/></svg></div>
    <div class="end-call"><svg width="56" height="22" viewBox="0 0 56 22" fill="#fff"><path d="M2 14c14-14 38-14 52 0l-3 7-9-3-1-5c-8-3-18-3-26 0l-1 5-9 3z"/></svg></div>
    <div class="ctrl" style="left:398px"><svg width="20" height="14" viewBox="0 0 20 14" fill="#fff"><rect x="0" y="2" width="13" height="10" rx="1.5"/><path d="M14 6l6-4v10l-6-4z"/></svg></div>
    <div class="ctrl" style="left:471px"><svg width="18" height="18" viewBox="0 0 24 24" fill="#fff"><path d="M10 1h4l.6 3 2.4 1 2.6-1.7 2.8 2.8L20.7 8.7 21.7 11l3 .6v4l-3 .6-1 2.4 1.7 2.6-2.8 2.8-2.6-1.7-2.4 1L14 24h-4l-.6-3-2.4-1-2.6 1.7-2.8-2.8L3.3 16.3 2.3 14l-3-.6v-4l3-.6 1-2.4L1.6 3.8 4.4 1l2.6 1.7 2.4-1zM12 8a4.5 4.5 0 1 0 0 9 4.5 4.5 0 0 0 0-9z" transform="translate(0 -.5) scale(.96)"/></svg></div>
  </section>

  <section class="now">
    <svg width="50" height="46" viewBox="0 0 50 46" stroke="#8a2f72" stroke-width="2" stroke-linecap="round"><path d="M2 18v10M8 12v22M14 6v34M20 14v18M26 2v42M32 10v26M38 16v14M44 8v30M49 20v6"/></svg>
    <div><p class="now-head">Now</p><p class="now-text">Sed ut perspiciatis unde omnis iste natus error sit voluptatem accusantium doloremque</p></div>
  </section>

  <aside class="chat">
    <div class="chat-head"><span class="chat-title">Group Chat</span><span class="tab active">Messages</span><span class="tab" style="padding-left:8px">Participants</span></div>
    <div class="messages">
      <p class="sender">Mira Castell</p>
      <div class="msg"><span class="avatar blue" role="img" aria-label="Mira Castell avatar"></span><span class="bubble">Hey! I'm waiting 😊</span></div>
      <p class="sender">Owen Pryce</p>
      <div class="msg"><span class="avatar" style="visibility:hidden"></span><span class="bubble">Hello all!</span></div>
      <div class="msg" style="margin-bottom:18px"><span class="avatar amber" role="img" aria-label="Owen Pryce avatar"></span><span class="bubble">Are we waiting for absent teammates?</span></div>
      <p class="sender">Mira Castell</p>
      <div class="msg"><span class="avatar blue" role="img" aria-label="Mira Castell avatar"></span><span class="bubble">Hey! I'm waiting 😊</span></div>
      <p class="sender">Owen Pryce</p>
      <div class="msg"><span class="avatar" style="visibility:hidden"></span><span class="bubble">Hello all!</span></div>
      <div class="msg" style="margin-bottom:18px"><span class="avatar amber" role="img" aria-label="Owen Pryce avatar"></span><span class="bubble">Are we waiting for absent teammates?</span></div>
      <p class="sender">Mira Castell</p>
      <div class="msg"><span class="avatar blue" role="img" aria-label="Mira Castell avatar"></span><span class="bubble call"><span class="call-icon"><svg width="12" height="12" viewBox="0 0 24 24" fill="#2aa889"><path d="M6 2l4 5-2 3a12 12 0 0 0 6 6l3-2 5 4-2 4C10 22 2 14 2 4z"/></svg></span>Started the call</span></div>
    </div>
    <div class="composer"><span>Write your Messages</span><span class="send"><svg width="18" height="18" viewBox="0 0 24 24" fill="#fff"><path d="M22 2L2 10l8 3 3 9z"/></svg></span></div>
  </aside>
</main>
</body>
</html>
```